Stationery Design Project for Nimbora, Chicago

Nimbora, a street parking application which helps car drivers find a street parking spot by offering an ideal path along which to look for parking. This path is calculated by our algorithm based on data (e.g. historical data, baseball games schedule, etc.). Along this path the driver will find a spot and will also save 70% of the search time. Customer we target is reg. between 21 and 45 yo.

We envision something young, fresh, bright and original. Slightly abstract maybe. It should represent the idea and elements of finding street parking in the city, e.g. car(s), parking spot, people, city, etc. (just ideas!).

Logo is attached.

Requirement:
- Business Cards (2 Sided Full Color CMYK)
- Letterhead (1 Sided Full Color CMYK)
- Envelope (1 Sided Full Color CMYK)
- Sticker (1 Sided Full Color CMYK), round with a 2inch diameter.

Reason: We're starting to get more and more designs and need more time to look into all of them. Very exciting!! Thanks to everybody!

Hi all, we're in the process of selecting our favs. Though choices!!! Really good submissions. Will keep you posted and sorry for the delay.

Target Market(s)

Car drivers and owners between 21 and 45

Industry/Entity Type

Parking

Requirements
Must have
• Sticker should be round and include company URL nimbora.com and the new logo which we will attach soon.
Should not have
• Should not be too serious or boring.

```html
<!DOCTYPE html>
<html lang="en">
<head>
<meta charset="utf-8">
<title>Nimbora — Business Card</title>
<link rel="stylesheet" href="https://fonts.googleapis.com/css2?family=Arimo:wght@400;700&display=swap">
<style>
  :root {
    --stage: #e9e7e3;
    --card-white: #f4f4f4;
    --ink: #2b2b2b;
    --ink-soft: #4a4a4a;
    --rule: #6a6a6a;
    --brand-blue: #1f6fd1;
    --deep-blue: #1d2a9e;
    --mid-blue: #1560c8;
    --light-blue: #27a8e0;
  }
  * { box-sizing: border-box; margin: 0; padding: 0; }
  html, body {
    width: 1200px;
    height: 720px;
    overflow: hidden;
    background: var(--stage);
    font-family: "Arimo", Arial, sans-serif;
  }
  .sheet {
    width: 1200px;
    height: 720px;
    display: flex;
    align-items: center;
    justify-content: center;
    gap: 40px;
  }
  .card {
    position: relative;
    width: 520px;
    height: 297px;
    box-shadow: 0 6px 18px rgba(0,0,0,0.18);
  }
  .card-front { background: var(--card-white); color: var(--ink); }
  .brand {
    position: absolute;
    left: 30px;
    top: 30px;
    display: flex;
    align-items: center;
    gap: 16px;
  }
  .brand-dot {
    width: 58px;
    height: 58px;
    border-radius: 50%;
    background: var(--brand-blue);
  }
  .brand-name {
    font-size: 40px;
    font-weight: 700;
    color: var(--ink);
    letter-spacing: 0.5px;
  }
  .rule-top {
    position: absolute;
    left: 190px;
    right: 28px;
    top: 104px;
    height: 1px;
    background: var(--rule);
  }
  .holder {
    position: absolute;
    left: 34px;
    top: 118px;
    font-size: 19px;
    color: var(--ink-soft);
  }
  .rule-name {
    position: absolute;
    left: 30px;
    width: 220px;
    top: 146px;
    height: 1px;
    background: var(--rule);
  }
  .address {
    position: absolute;
    left: 318px;
    top: 120px;
    font-size: 12.5px;
    line-height: 24px;
    color: var(--ink);
  }
  .contacts {
    position: absolute;
    left: 34px;
    top: 166px;
    list-style: none;
    font-size: 14px;
    color: var(--ink-soft);
  }
  .contacts li {
    display: flex;
    align-items: center;
    gap: 14px;
    height: 24px;
  }
  .contacts svg { width: 14px; height: 14px; flex: none; }
  .card-back {
    background:
      radial-gradient(circle at 62% 45%, var(--light-blue) 0%, var(--mid-blue) 45%, var(--deep-blue) 100%);
  }
</style>
</head>
<body>
  <main class="sheet">
    <section class="card card-front" aria-label="Business card front">
      <div class="brand">
        <span class="brand-dot"></span>
        <span class="brand-name">Nimbora</span>
      </div>
      <div class="rule-top"></div>
      <p class="holder">Maren Holt Vandeberg</p>
      <div class="rule-name"></div>
      <p class="address">1420 West Lake Street,<br>Chicago, IL 60607</p>
      <ul class="contacts">
        <li>
          <svg viewBox="0 0 14 14" aria-hidden="true"><rect x="3" y="0.5" width="8" height="13" rx="1.5" fill="none" stroke="#3a3a3a" stroke-width="1.4"/><rect x="4.6" y="2.3" width="4.8" height="4" fill="#3a3a3a"/></svg>
          <span>+31 612 480 375</span>
        </li>
        <li>
          <svg viewBox="0 0 14 14" aria-hidden="true"><rect x="0.7" y="2.5" width="12.6" height="9" fill="none" stroke="#3a3a3a" stroke-width="1.4"/><path d="M0.7 2.5 L7 8 L13.3 2.5" fill="none" stroke="#3a3a3a" stroke-width="1.4"/></svg>
          <span>maren@nimbora.com</span>
        </li>
        <li>
          <svg viewBox="0 0 14 14" aria-hidden="true"><path d="M7 1 L13.5 7 H11.5 V13 H8.5 V9 H5.5 V13 H2.5 V7 H0.5 Z" fill="#3a3a3a"/></svg>
          <span>www.nimbora.com</span>
        </li>
      </ul>
    </section>
    <section class="card card-back" role="img" aria-label="Abstract blue artwork of overlapping light-blue outlined shapes on a deep blue field"></section>
  </main>
</body>
</html>
```